I have a business that exists already (Linden Conservatory of Music) that we offer music lessons to all instruments. I recently opened a smaller version called CHORDS by Linden that will only teach piano lessons. What I'm looking for now is a 3 page Website on word press. After I choose the design I like I want to be able to take over the website and bring it to our hosting company. We want full control of it and our team will take over. The reason I'm doing this is to have other visions and ideas from others. The first page will be about the company and our message/vision. Second page about the piano lessons. The third will be about franchising this concept "Chords by Linden" Attached are 3 Logos . Please refer to our existing website www.lindenmusicconservatory.example to look at our piano page and franchising page. Please feel free to message me if you need more info. Thanks
Please note I do not want the new website (Chords by Linden) To look like the other Website (Linden Conservatory of Music) Fresh new look. I do not want the colours red or using the Red logo. I only provided it so that you have an Idea of What the other business looks like and that you can take the piano content and franchise content off of it. Chords by Linden is smaller concept and only piano lessons.
Thanks
Only Piano lessons for all students
3 page

```html
<!DOCTYPE html>
<html lang="en">
<head>
<meta charset="utf-8">
<title>Chords by Linden — Piano Lessons</title>
<link rel="stylesheet" href="https://fonts.googleapis.com/css2?family=Lora:ital,wght@0,400;0,500;1,400&family=Lobster&family=Montserrat:wght@400;500&display=swap">
<style>
:root{
  --black:#000;
  --teal:#58c6bb;
  --gold:#e7c45f;
  --gold-footer:#e8c766;
  --sand:#eeede9;
  --ink:#1c1c1c;
  --muted:#3a3a3a;
  --white:#fff;
  --slate:#585858;
  --pale:#efefef;
}
*{margin:0;padding:0;box-sizing:border-box}
html,body{width:1200px;height:3428px;overflow:hidden;background:var(--white)}
.canvas{position:relative;width:1200px;height:3428px;overflow:hidden;font-family:'Lora',serif;color:var(--ink)}
.abs{position:absolute}
.site-header{left:0;top:0;width:1200px;height:76px;background:var(--black)}
.brand{left:143px;top:14px;color:var(--white);font-family:'Lora',serif;font-size:26px;line-height:44px;display:flex;align-items:center;gap:8px}
.brand-mark{width:12px;height:12px;background:var(--white)}
.nav{right:142px;top:30px;display:flex;gap:37px;font-size:14px;color:var(--white);letter-spacing:.2px}
.nav a{color:inherit;text-decoration:none}
.nav .active{color:var(--teal);font-weight:500}
.hero{left:0;top:76px;width:1200px;height:549px;background:radial-gradient(ellipse at 50% 40%,#5a3722 0%,#3a2416 45%,#1a100a 100%)}
.hero-title{left:0;width:1200px;text-align:center;color:var(--white);font-family:'Lobster',cursive;font-style:italic}
.btn{display:flex;align-items:center;justify-content:center;font-family:'Lora',serif;font-size:14px;letter-spacing:.4px;text-transform:uppercase;color:var(--white);background:var(--teal)}
.btn-gold{background:var(--gold);color:var(--ink);font-size:13px}
.intro-band{left:0;top:625px;width:1200px;height:506px;background:var(--sand)}
.photo{}
.intro-card{left:579px;top:577px;width:480px;height:423px;background:var(--white);text-align:center}
.intro-card h2{font-weight:400;font-size:33px;margin-top:42px}
.intro-card p{font-size:12.6px;line-height:23px;margin:12px 38px 0}
.intro-card p+p{margin-top:6px}
.scroll-cue{left:573px;top:1032px}
h2.section-title{font-weight:400;font-size:33px;line-height:40px}
.body-copy{font-size:12.8px;line-height:25.5px;color:var(--muted)}
.teal-frame{background:var(--teal)}
.frame-line{border:1.5px solid var(--white)}
.program-list{list-style:none;font-size:13.5px;line-height:22.5px;color:var(--muted)}
.program-list li{position:relative;padding-left:25px;margin-bottom:9px}
.program-list svg{position:absolute;left:0;top:5px}
.quote-card{left:141px;top:2135px;width:918px;height:211px;background:var(--white);border-radius:18px;box-shadow:0 4px 22px rgba(0,0,0,.12);text-align:center}
.quote-mark{left:90px;top:-60px;font-size:210px;color:#f0f0f0;font-family:'Lora',serif;line-height:1}
.quote-text{position:relative;font-style:italic;font-size:21px;line-height:38px;margin:46px 160px 0;color:var(--ink)}
.quote-author{position:relative;color:var(--teal);font-size:17px;letter-spacing:.5px;margin-top:14px}
.franchise{left:0;top:2420px;width:1200px;height:267px;background:linear-gradient(180deg,#ececec,#f2f2f2)}
.band-title{left:0;width:1200px;text-align:center;font-weight:400;text-transform:uppercase}
.rule{width:38px;height:2px;background:var(--gold)}
.meeting{left:0;top:2687px;width:1200px;height:479px;background:linear-gradient(180deg,#1b1b1b 0%,#2c2c2c 33%,var(--slate) 33%,var(--slate) 100%)}
.form-card{left:141px;top:2826px;width:918px;height:270px;background:var(--white)}
.field{background:var(--white);box-shadow:0 2px 8px rgba(0,0,0,.12);font-family:'Montserrat',sans-serif;font-size:11px;color:#777;padding:14px 14px}
.site-footer{left:0;top:3166px;width:1200px;height:262px;background:var(--gold-footer)}
.contact-item{top:3210px;width:300px;text-align:center;font-size:14px;color:var(--ink)}
.contact-item h3{font-weight:400;font-size:15px;margin-top:18px;letter-spacing:.3px}
.contact-item p{font-family:'Montserrat',sans-serif;font-size:12.5px;line-height:21px}
.footer-rule{left:141px;top:3376px;width:918px;height:1px;background:rgba(0,0,0,.25)}
.copyright{left:141px;top:3399px;font-family:'Montserrat',sans-serif;font-size:12px}
.social{top:3390px;width:31px;height:31px;border-radius:50%;background:var(--black)}
</style>
</head>
<body>
<div class="canvas">

  <header class="abs site-header">
    <div class="abs brand"><span class="brand-mark"></span>CHORDS by Linden</div>
    <nav class="abs nav">
      <a class="active" href="#">HOME</a>
      <a href="#">PIANO LESSONS</a>
      <a href="#">FRANCHISING</a>
      <a href="#">CONTACT US</a>
    </nav>
  </header>

  <section class="abs hero" role="img" aria-label="Close view of a wooden upright piano keyboard in warm low light">
  </section>
  <h1 class="abs hero-title" style="top:312px;font-size:44px;font-weight:400">We Provide Piano Lessons</h1>
  <p class="abs hero-title" style="top:372px;font-size:33px">For All Students</p>
  <a class="abs btn" style="left:502px;top:431px;width:196px;height:40px">Contact Us Today</a>

  <section class="abs intro-band"></section>
  <div class="abs photo" style="left:141px;top:577px;width:438px;height:423px;background:linear-gradient(135deg,#2d3a3c 0%,#6b6e6a 40%,#d8d2c8 75%,#2a2a2a 100%)" role="img" aria-label="Two hands playing the keys of a piano"></div>
  <article class="abs intro-card">
    <h2>Playing The Piano</h2>
    <p>When you think of a piano, you probably envision black and white keys but the piano is more than those harmonious sounds created by the player.</p>
    <p>The versatility and the musicianship instilled into the player from those keys is the true magic that comes from playing piano! Starting from the grassroots, experience different methods and styles of playing piano. To mark the milestones of progression, engage in one of Linden’s many unique performance opportunities like annual festival competitions, recitals or our examinations (Linden &amp; NCE). Penultimately, at the end of the journey, join our elite teaching program to bring the same joy of learning the piano to another student.</p>
  </article>
  <svg class="abs scroll-cue" width="54" height="54" viewBox="0 0 54 54" aria-hidden="true">
    <rect x="12" y="12" width="30" height="30" transform="rotate(45 27 27)" fill="none" stroke="#cfcdc6" stroke-width="1.5"/>
    <path d="M27 20v13M22 28l5 5 5-5" fill="none" stroke="#bdbab2" stroke-width="1.5"/>
  </svg>

  <section>
    <h2 class="abs section-title" style="left:143px;top:1238px">Our Vision</h2>
    <div class="abs body-copy" style="left:143px;top:1291px;width:485px">
      <p>Lorem ipsum dolor sit amet, consectetur adipiscing elit. In hendrerit, odio utrtyy semper consequat, justo dui convallis ligula, ac congue felis ipsum sed felis. Cura volutpat leo faucibus magna elementum ultrices.</p>
      <p style="margin-top:6px">Cras eleifend faucibus lacus convallis elementum. Phasellus vitae lobortis donece in risus sit amet enim eleifend semper sed id ipsum. Ut ac placerat nisl pellentesq venenatis ligula eget turpis aliquam ornare. Vivamus tincidunt tellus at rutrum fd aliquam. Etiam ullamcorper consequat felis vitae posuere. Nunc nec facilisis nuni, at dignissim augue. Sed sed orci felis. Aliquam quis auctor ipsum.</p>
    </div>
    <a class="abs btn" style="left:141px;top:1514px;width:169px;height:35px;font-size:13px">Contact Us Today</a>
    <div class="abs teal-frame" style="left:741px;top:1209px;width:317px;height:318px"></div>
    <div class="abs frame-line" style="left:722px;top:1227px;width:318px;height:300px;border-left:none;border-bottom:none"></div>
    <div class="abs photo" style="left:678px;top:1270px;width:317px;height:316px;background:linear-gradient(160deg,#f3ece4 0%,#e8a58e 45%,#f2c8cf 70%,#3d3b3b 100%)" role="img" aria-label="A teacher smiling with two young students at a piano"></div>
  </section>

  <section>
    <div class="abs teal-frame" style="left:141px;top:1654px;width:318px;height:318px"></div>
    <div class="abs frame-line" style="left:160px;top:1672px;width:299px;height:300px;border-right:none;border-bottom:none"></div>
    <div class="abs photo" style="left:204px;top:1715px;width:317px;height:315px;background:linear-gradient(135deg,#f4f4f4 0%,#b88a6a 35%,#27304a 60%,#e9e6e1 100%)" role="img" aria-label="Two young women playing piano together"></div>
    <h2 class="abs section-title" style="left:576px;top:1646px;width:490px">Our Programs Also Provide Students The Opportunity To</h2>
    <ul class="abs program-list" style="left:576px;top:1739px;width:470px">
      <li><svg width="14" height="14" viewBox="0 0 14 14"><circle cx="7" cy="7" r="5.5" fill="none" stroke="#444" stroke-width="1.2"/><path d="M4 7l2.3 2.3L12 3" fill="none" stroke="#444" stroke-width="1.4"/></svg>Participate in large-scale performances.</li>
      <li><svg width="14" height="14" viewBox="0 0 14 14"><circle cx="7" cy="7" r="5.5" fill="none" stroke="#444" stroke-width="1.2"/><path d="M4 7l2.3 2.3L12 3" fill="none" stroke="#444" stroke-width="1.4"/></svg>Perform at Linden’s many community events on a regular basis.</li>
      <li><svg width="14" height="14" viewBox="0 0 14 14"><circle cx="7" cy="7" r="5.5" fill="none" stroke="#444" stroke-width="1.2"/><path d="M4 7l2.3 2.3L12 3" fill="none" stroke="#444" stroke-width="1.4"/></svg>Access the city’s coolest Broadcast stage</li>
      <li><svg width="14" height="14" viewBox="0 0 14 14"><circle cx="7" cy="7" r="5.5" fill="none" stroke="#444" stroke-width="1.2"/><path d="M4 7l2.3 2.3L12 3" fill="none" stroke="#444" stroke-width="1.4"/></svg>Attend Clinics, Masterclasses, and Jam Nights</li>
      <li><svg width="14" height="14" viewBox="0 0 14 14"><circle cx="7" cy="7" r="5.5" fill="none" stroke="#444" stroke-width="1.2"/><path d="M4 7l2.3 2.3L12 3" fill="none" stroke="#444" stroke-width="1.4"/></svg>Access the Linden Live band program. Linden’s Band Program empowers and electrifies students to come together, create music and confidently hit the stage with their own band identity while having fun and honing their instrument.</li>
      <li><svg width="14" height="14" viewBox="0 0 14 14"><circle cx="7" cy="7" r="5.5" fill="none" stroke="#444" stroke-width="1.2"/><path d="M4 7l2.3 2.3L12 3" fill="none" stroke="#444" stroke-width="1.4"/></svg>Register in our elite teaching program to learn how to pass on the magic and passion of playing the piano to students.</li>
    </ul>
    <a class="abs btn" style="left:575px;top:2029px;width:169px;height:34px;font-size:13px">Contact Us Today</a>
  </section>

  <blockquote class="abs quote-card">
    <span class="abs quote-mark" aria-hidden="true">“</span>
    <p class="quote-text">“Life is like a piano. What you get out of it depends on how you play it.”</p>
    <p class="quote-author">THEO MARLOW</p>
  </blockquote>

  <section class="abs franchise" role="img" aria-label="Soft, faded background of hands on piano keys">
  </section>
  <h2 class="abs band-title" style="top:2483px;font-size:31px;color:var(--ink)">Franchise Opportunities</h2>
  <div class="abs rule" style="left:581px;top:2530px"></div>
  <p class="abs" style="left:0;top:2545px;width:1200px;text-align:center;font-family:'Montserrat',sans-serif;font-size:15px;color:#444;letter-spacing:.3px">Be Part Of The Linden Conservatory Family</p>
  <a class="abs btn btn-gold" style="left:543px;top:2582px;width:114px;height:35px">Read More</a>

  <section class="abs meeting" role="img" aria-label="Dark photograph of piano keys">
  </section>
  <h2 class="abs band-title" style="top:2752px;font-size:24px;color:var(--white);letter-spacing:.3px">Book A Meeting With Us</h2>
  <div class="abs rule" style="left:581px;top:2790px"></div>
  <form class="abs form-card">
    <div class="abs field" style="left:48px;top:26px;width:267px;height:40px">Your Name*</div>
    <div class="abs field" style="left:324px;top:26px;width:268px;height:40px">Your Phone*</div>
    <div class="abs field" style="left:604px;top:26px;width:269px;height:40px">Your Email*</div>
    <div class="abs field" style="left:48px;top:80px;width:825px;height:86px">Your Message*</div>
    <a class="abs btn btn-gold" style="left:401px;top:198px;width:116px;height:35px">Submit</a>
  </form>

  <footer class="abs site-footer"></footer>
  <div class="abs contact-item" style="left:106px">
    <svg width="46" height="46" viewBox="0 0 46 46" aria-hidden="true"><path d="M12 6l6 8-4 4c2 6 6 10 12 13l4-4 8 6-4 7C21 39 7 25 5 10z" fill="#111"/><path d="M26 8a12 12 0 0 1 12 12M26 14a6 6 0 0 1 6 6" fill="none" stroke="#111" stroke-width="2.5"/></svg>
    <h3>CALL US</h3>
    <p>1-800-555-0142</p>
  </div>
  <div class="abs contact-item" style="left:450px">
    <svg width="46" height="50" viewBox="0 0 46 50" aria-hidden="true"><path d="M23 2C13 2 7 9 7 17c0 12 16 31 16 31s16-19 16-31C39 9 33 2 23 2z" fill="#111"/><circle cx="23" cy="17" r="6" fill="var(--gold-footer)"/></svg>
    <h3>POSTAL ADDRESS</h3>
    <p>123, Lorem ipsum dolor sit 123456<br>#123456 Lorem ipsum</p>
  </div>
  <div class="abs contact-item" style="left:760px">
    <svg width="46" height="46" viewBox="0 0 46 46" aria-hidden="true"><rect x="2" y="8" width="42" height="30" rx="3" fill="#111"/><path d="M4 11l19 15 19-15" fill="none" stroke="var(--gold-footer)" stroke-width="2.5"/></svg>
    <h3>E-MAIL</h3>
    <p>hello@chordslinden.example</p>
  </div>
  <div class="abs footer-rule"></div>
  <p class="abs copyright">Copyright 2019. Chordslinden Music Training. All rights reserved.</p>
  <span class="abs social" style="left:950px" aria-label="Social link"></span>
  <span class="abs social" style="left:989px" aria-label="Social link"></span>
  <span class="abs social" style="left:1028px" aria-label="Social link"></span>

</div>
</body>
</html>
```